landscaping core flute signs

I need core flutes created with business name and a few extra dot points for putting on fences for job sites 120cm x 120cm approx.
I want our old ones information with the new L logo and colour palette

```html
<!DOCTYPE html>
<html lang="en">
<head>
<meta charset="utf-8">
<title>Keystone Grounds – Site Sign</title>
<link href="https://fonts.googleapis.com/css2?family=Arimo:wght@400;700&display=swap" rel="stylesheet">
<style>
  :root {
    --backdrop: #eeeeee;
    --sign-white: #ffffff;
    --ink: #111111;
    --leaf-green: #5e8c58;
    --tab-text: #ffffff;
  }
  * { margin: 0; padding: 0; box-sizing: border-box; }
  html, body {
    width: 1200px;
    height: 829px;
    overflow: hidden;
    background: var(--backdrop);
    font-family: "Arimo", Arial, sans-serif;
    color: var(--ink);
  }
  .sign {
    position: absolute;
    left: 202px;
    top: 16px;
    width: 796px;
    height: 796px;
    background: var(--sign-white);
    overflow: hidden;
  }
  .brand-dot {
    position: absolute;
    left: 298px;
    top: 36px;
    width: 200px;
    height: 200px;
    border-radius: 50%;
    background: var(--leaf-green);
  }
  .brand-name {
    position: absolute;
    left: 0;
    width: 100%;
    text-align: center;
    color: var(--ink);
    font-weight: 400;
    line-height: 1;
  }
  .brand-name--main { top: 258px; font-size: 58px; letter-spacing: 1px; }
  .brand-name--sub { top: 316px; font-size: 32px; letter-spacing: 10px; }
  .tagline {
    position: absolute;
    top: 355px;
    left: 0;
    width: 100%;
    text-align: center;
    font-size: 15px;
    letter-spacing: 4.5px;
    color: var(--leaf-green);
  }
  .services {
    position: absolute;
    left: 222px;
    top: 414px;
    list-style: none;
  }
  .service {
    display: flex;
    align-items: center;
    height: 62px;
    font-size: 31px;
  }
  .service svg { width: 38px; height: 38px; margin-right: 12px; flex: none; }
  .phone {
    position: absolute;
    top: 598px;
    left: 0;
    width: 100%;
    text-align: center;
    font-size: 70px;
    font-weight: 700;
    letter-spacing: 1px;
  }
  .email {
    position: absolute;
    top: 686px;
    left: 0;
    width: 100%;
    text-align: center;
    font-size: 35px;
    font-weight: 700;
  }
  .footer-band {
    position: absolute;
    left: 0;
    top: 740px;
    width: 796px;
    height: 56px;
  }
  .licence {
    position: absolute;
    top: 756px;
    left: 0;
    width: 100%;
    text-align: center;
    font-size: 24px;
    font-weight: 700;
    color: var(--tab-text);
  }
</style>
</head>
<body>
  <main class="sign">
    <div class="brand-dot"></div>
    <div class="brand-name brand-name--main">KEYSTONE</div>
    <div class="brand-name brand-name--sub">GROUNDS</div>
    <div class="tagline">STRUCTURAL LANDSCAPING</div>

    <ul class="services">
      <li class="service">
        <svg viewBox="0 0 38 38" aria-hidden="true"><circle cx="18" cy="20" r="15" fill="none" stroke="var(--leaf-green)" stroke-width="3"/><path d="M10 20 L17 28 L33 5" fill="none" stroke="var(--leaf-green)" stroke-width="4" stroke-linecap="round" stroke-linejoin="round"/></svg>
        Paving &amp; Concreting
      </li>
      <li class="service">
        <svg viewBox="0 0 38 38" aria-hidden="true"><circle cx="18" cy="20" r="15" fill="none" stroke="var(--leaf-green)" stroke-width="3"/><path d="M10 20 L17 28 L33 5" fill="none" stroke="var(--leaf-green)" stroke-width="4" stroke-linecap="round" stroke-linejoin="round"/></svg>
        Fencing &amp; Retaining
      </li>
      <li class="service">
        <svg viewBox="0 0 38 38" aria-hidden="true"><circle cx="18" cy="20" r="15" fill="none" stroke="var(--leaf-green)" stroke-width="3"/><path d="M10 20 L17 28 L33 5" fill="none" stroke="var(--leaf-green)" stroke-width="4" stroke-linecap="round" stroke-linejoin="round"/></svg>
        &nbsp;Desgin &amp; Construct
      </li>
    </ul>

    <div class="phone">0412 555 019</div>
    <div class="email">sam@keystonegrounds.com</div>

    <svg class="footer-band" viewBox="0 0 796 56" aria-hidden="true">
      <rect x="0" y="15" width="796" height="6" fill="var(--ink)"/>
      <rect x="0" y="35" width="796" height="21" fill="var(--leaf-green)"/>
      <polygon points="262,35 286,10 510,10 534,35" fill="var(--sign-white)"/>
      <polygon points="268,36 290,14 506,14 528,36" fill="var(--leaf-green)"/>
    </svg>
    <div class="licence">QBSA:&nbsp; 1098342</div>
  </main>
</body>
</html>
```